Looking for a dynamic business card for a pizzeria.

A business card with our food, logo, and space for name, title, email, website, phone. The card should convey quality, unique, amazing. On the front, I envision food photo or photos with the owners names and contact information. On the back, more food with locations, website, facebook, twitter, instagram icons. It should look polished, not cartoonish, or plain.
Target Market(s)
upscale, local food buyers, 30-50 years in age.
Industry/Entity Type
Restaurant
Contact Information for Business Card
Business Name: Bru'nettix, LLC
Website: www.brunettix.com
Back:
2 locations: (can list on the back of card)
1. LAKEMONT
4087 Corlan Avenue
Harlow, WA 98471
360-481-5067
2. CEDAR RISE
7315 Wendmere Road
Harlow, WA 98476
360-293-8840
front:
EDITABLE space for
Business name
Person's Name
title
2nd title
Email address
cell-phone number
Requirements
Must have
- logo
- my food photo or photos (no watermarks showing)
- locations on back
- Person contact information on front
- full bleed

```html
<!DOCTYPE html>
<html lang="en">
<head>
<meta charset="utf-8">
<title>Bru'nettix Business Card</title>
<link href="https://fonts.googleapis.com/css2?family=Questrial&family=Arimo:wght@400;700&display=swap" rel="stylesheet">
<style>
  :root {
    --green: #1f4d22;
    --red: #b3242a;
    --ink: #222222;
    --paper: #ffffff;
    --backdrop: #ece7df;
    --text-font: "Questrial", sans-serif;
    --head-font: "Arimo", sans-serif;
  }
  * { box-sizing: border-box; margin: 0; padding: 0; }
  html, body { width: 1189px; height: 1200px; overflow: hidden; background: var(--backdrop); }
  .canvas { position: relative; width: 1189px; height: 1200px; }
  .card { position: absolute; left: 144px; width: 901px; height: 514px; background: var(--paper); overflow: hidden; }
  .card--front { top: 46px; }
  .card--back { top: 640px; }

  /* Front */
  .brand { position: absolute; left: 60px; top: 78px; }
  .brand__name { font-family: var(--text-font); font-size: 62px; color: var(--green); letter-spacing: 1px; line-height: 1; }
  .person { position: absolute; right: 56px; top: 42px; text-align: right; }
  .person__name { font-family: var(--head-font); font-weight: 700; font-size: 40px; color: var(--green); line-height: 1; }
  .person__title { font-family: var(--text-font); font-size: 26px; color: var(--red); line-height: 1.1; margin-top: 2px; }
  .person__phone { display: flex; justify-content: flex-end; align-items: center; gap: 12px; margin-top: 18px; font-family: var(--text-font); font-size: 26px; color: var(--ink); }
  .rule-thick { position: absolute; left: 0; right: 0; top: 194px; height: 9px; background: var(--green); }
  .photo-band { position: absolute; left: 0; right: 0; top: 208px; height: 226px; background: var(--green); display: grid; grid-template-columns: repeat(4, 1fr); gap: 4px; padding: 4px 0; }
  .photo { height: 100%; }
  .photo--sandwich { background: linear-gradient(135deg, #6b4a2c, #c9933e 55%, #4f6b2a); }
  .photo--oven { background: linear-gradient(180deg, #e7a04a, #a8482a 55%, #d9c2a3); }
  .photo--pepperoni { background: linear-gradient(160deg, #8a6a5a, #d07a5c 45%, #ecd9c4); }
  .photo--peppers { background: linear-gradient(135deg, #e5d46c, #6aa637 45%, #5a3424 80%); }
  .contact-bar { position: absolute; left: 0; right: 0; bottom: 0; height: 74px; background: var(--green); border-top: 5px solid var(--paper); display: flex; justify-content: space-between; align-items: center; padding: 0 56px 0 60px; }
  .contact-bar__item { display: flex; align-items: center; gap: 14px; font-family: var(--text-font); font-size: 26px; color: var(--paper); }

  /* Back */
  .hero { position: absolute; left: 0; right: 0; top: 0; height: 242px; background: linear-gradient(100deg, #7d7a74 0%, #b9a58a 40%, #c8ad86 60%, #6b5a4a 100%); }
  .hero__band { position: absolute; left: 0; right: 0; top: 79px; height: 83px; background: rgba(255,255,255,0.35); display: flex; align-items: center; justify-content: center; }
  .hero__name { font-family: var(--head-font); font-size: 60px; color: var(--green); letter-spacing: 1px; }
  .social { position: absolute; left: 0; right: 0; top: 186px; display: flex; justify-content: center; gap: 21px; }
  .social__tile { width: 36px; height: 36px; border-radius: 3px; background: var(--green); }
  .locations { position: absolute; left: 0; right: 0; top: 274px; display: grid; grid-template-columns: 440px 1fr; }
  .location { font-family: var(--text-font); font-size: 26px; color: var(--ink); line-height: 1.2; }
  .location--left { text-align: right; padding-right: 30px; border-right: 3px solid var(--green); }
  .location--right { padding-left: 30px; }
  .location__name { font-family: var(--head-font); font-weight: 700; font-size: 26px; color: var(--green); margin-bottom: 16px; letter-spacing: -0.5px; }
  .location__phone { margin-top: 8px; }
  .web-bar { position: absolute; left: 0; right: 0; bottom: 0; height: 69px; background: var(--green); display: flex; align-items: center; justify-content: center; font-family: var(--text-font); font-size: 24px; color: var(--paper); letter-spacing: 0.5px; }
</style>
</head>
<body>
<div class="canvas">

  <section class="card card--front">
    <div class="brand">
      <span class="brand__name">BRU'NETTIX</span>
    </div>
    <div class="person">
      <div class="person__name">Employee Name</div>
      <div class="person__title">Managing Director</div>
      <div class="person__phone">
        <span>123 456 7890</span>
        <svg width="28" height="28" viewBox="0 0 28 28" aria-hidden="true">
          <rect width="28" height="28" fill="#1f4d22"/>
          <rect x="9" y="4" width="10" height="20" rx="2" fill="none" stroke="#fff" stroke-width="2"/>
          <rect x="11" y="7" width="6" height="6" fill="#fff"/>
        </svg>
      </div>
    </div>
    <div class="rule-thick"></div>
    <div class="photo-band">
      <div class="photo photo--sandwich" role="img" aria-label="Photo of a grilled panini sandwich"></div>
      <div class="photo photo--oven" role="img" aria-label="Photo of pizza rolls baking by the oven fire"></div>
      <div class="photo photo--pepperoni" role="img" aria-label="Photo of a hand placing pepperoni on pizza dough"></div>
      <div class="photo photo--peppers" role="img" aria-label="Photo of roast beef with green peppers and red onion"></div>
    </div>
    <div class="contact-bar">
      <div class="contact-bar__item">
        <svg width="28" height="24" viewBox="0 0 28 24" aria-hidden="true">
          <rect width="28" height="24" fill="#fff"/>
          <rect x="4" y="5" width="20" height="14" fill="none" stroke="#1f4d22" stroke-width="2"/>
          <path d="M4 5 L14 13 L24 5 M4 19 L11 11 M24 19 L17 11" fill="none" stroke="#1f4d22" stroke-width="1.6"/>
        </svg>
        <span>you@brunettix.com</span>
      </div>
      <div class="contact-bar__item">
        <svg width="28" height="28" viewBox="0 0 28 28" aria-hidden="true">
          <rect width="28" height="28" fill="#fff"/>
          <circle cx="14" cy="14" r="9" fill="none" stroke="#1f4d22" stroke-width="1.8"/>
          <ellipse cx="14" cy="14" rx="4" ry="9" fill="none" stroke="#1f4d22" stroke-width="1.4"/>
          <path d="M5 14 H23 M7 9 H21 M7 19 H21" stroke="#1f4d22" stroke-width="1.4"/>
        </svg>
        <span>www.brunettix.com</span>
      </div>
    </div>
  </section>

  <section class="card card--back">
    <div class="hero" role="img" aria-label="Photo of pizza dough being tossed with a dusting of flour">
      <div class="hero__band"><span class="hero__name">BRU'NETTIX, LLC</span></div>
      <div class="social">
        <span class="social__tile"></span>
        <span class="social__tile"></span>
        <span class="social__tile"></span>
      </div>
    </div>
    <div class="locations">
      <div class="location location--left">
        <div class="location__name">LAKEMONT</div>
        <div>4087 Corlan Avenue</div>
        <div>Harlow, WA 98471</div>
        <div class="location__phone">360-481-5067</div>
      </div>
      <div class="location location--right">
        <div class="location__name">CEDAR RISE</div>
        <div>7315 Wendmere Road</div>
        <div>Harlow, WA 98476</div>
        <div class="location__phone">360-293-8840</div>
      </div>
    </div>
    <div class="web-bar">www.brunettix.com</div>
  </section>

</div>
</body>
</html>
```